Celvara Health Group Presentation Folder, for Cancer Awareness, VERY COLORFUL AND MODERN

Presentation Folder I know pretty much what i want so it should be very eazy , I have included files from folders I use now rebrand them to my new company they will be fine, no sense re creating the wheel
Full Bleed Size
20.87" x 16.68"
53 x 42.4 cm
6260 x 5004 pixels
Document Trim Size
20.75" x 16.56"
52.7 x 42.1 cm
6225 x 4969 pixels

Low design quality

Industry/Entity Type

Medical

Font styles to use
Serif

Colors

Designer to choose colors to be used in the design.

Requirements
Must have
• really I am not looking for some one to redesign, we like our folder front page and would like to see new word information added., there are two folder front pages to choose from
• So Keep the original front page and redesign the back page and the pockets
• Can Make your Design off of one of the ones I already uploaded
Nice to have
• Keep the same color schemes, Keep the original front page and redesign the back page and the pockets
Should not have
• DO not recreate the front covers, use what I gave you and just rebrand

```html
<!DOCTYPE html>
<html lang="en">
<head>
<meta charset="utf-8">
<title>Celvara Health Group – Presentation Folder Dieline</title>
<link href="https://fonts.googleapis.com/css2?family=Raleway:wght@300;400;500;600;700;800&family=Open+Sans:wght@400;600;700&family=Fira+Sans:wght@400;500;600&display=swap" rel="stylesheet">
<style>
  :root{
    --bg-dark:#3f3f3f;
    --bg-light:#9b9b9b;
    --paper:#ffffff;
    --navy:#1b2a6b;
    --green:#8cc63f;
    --pink:#f297a8;
    --slate:#6d6e71;
    --ink:#222222;
    --muted:#6b6b6b;
    --guide:#9ad6ea;
    --cut:#e0393e;
    --fold:#5cc27a;
    --ribbon-a:#e86fc1;
    --ribbon-b:#4fb6e8;
  }
  *{box-sizing:border-box;margin:0;padding:0}
  html,body{width:1114px;height:1200px;overflow:hidden}
  body{
    position:relative;
    background:linear-gradient(160deg,var(--bg-dark) 0%,#5a5a5a 50%,var(--bg-light) 100%);
    font-family:"Open Sans",sans-serif;
    color:var(--ink);
  }
  .folder-body{position:absolute;left:0;top:0;filter:drop-shadow(2px 3px 4px rgba(0,0,0,.35))}
  .fold-line{position:absolute;border:0 dashed var(--fold)}
  .fold-line--spine{left:557px;top:55px;height:575px;border-left-width:1px}
  .fold-line--pocket{left:99px;top:630px;width:921px;border-top-width:1px}
  .guide{position:absolute;border:1px solid var(--guide)}
  .guide--left{left:111px;top:66px;width:431px;height:548px}
  .guide--right{left:572px;top:66px;width:432px;height:548px}

  .photo{position:absolute;box-shadow:2px 4px 8px rgba(0,0,0,.35)}
  .photo--beach{left:127px;top:162px;width:374px;height:248px;transform:rotate(-4deg);
    background:linear-gradient(180deg,#2a7fd0 0%,#5fb3ea 48%,#d9cdb4 62%,#c8b796 100%)}
  .photo--dinner{left:606px;top:250px;width:380px;height:256px;transform:rotate(-3deg);
    background:linear-gradient(180deg,#e9ece6 0%,#c9c0a9 45%,#a08d72 100%)}
  .ribbon{position:absolute;border-radius:14px 14px 4px 4px;
    background:linear-gradient(135deg,var(--ribbon-b) 0%,var(--ribbon-a) 100%)}
  .ribbon--left{left:462px;top:107px;width:36px;height:66px;transform:rotate(10deg)}
  .ribbon--right{left:947px;top:193px;width:30px;height:64px;transform:rotate(10deg)}

  .intro{position:absolute;left:151px;top:466px;width:362px;font-size:9.6px;line-height:1.36}
  .intro strong{color:var(--navy);font-weight:700}
  .intro__call{margin-top:9px;color:var(--navy);font-weight:600;font-size:10.2px;line-height:1.4}

  .title-band{position:absolute;left:557px;top:87px;width:500px;height:38px;background:var(--pink)}
  .title-band__text{position:absolute;left:15px;width:432px;top:0;line-height:38px;text-align:center;
    font-family:"Raleway",sans-serif;font-weight:700;font-size:20.5px;letter-spacing:1.4px;color:#fff}
  .lead{position:absolute;left:572px;width:432px;top:135px;text-align:center;font-family:"Raleway",sans-serif}
  .lead__head{font-size:13px;font-weight:500;color:var(--ink)}
  .lead__body{margin-top:7px;font-size:11px;font-weight:400;color:var(--muted);line-height:1.2;padding:0 40px}
  .tag-band{position:absolute;left:557px;top:538px;width:500px;height:32px;background:var(--slate)}
  .tag-band__text{position:absolute;left:117px;top:0;line-height:32px;font-family:"Fira Sans",sans-serif;
    font-size:15px;color:#fff;letter-spacing:.3px}
  .tag-band__dot{position:absolute;left:61px;top:11px;width:40px;height:40px;border-radius:50%;
    background:#fff;border:2px solid var(--navy)}

  .pocket{position:absolute;width:456px;height:217px;filter:drop-shadow(2px 3px 3px rgba(0,0,0,.35))}
  .pocket__sheet{position:absolute;inset:0}
  .pocket--white .pocket__sheet{background:var(--paper);clip-path:polygon(7% 0,100% 0,100% 100%,0 100%)}
  .pocket--green .pocket__sheet{background:var(--green);clip-path:polygon(0 0,91% 0,96% 9%,100% 100%,0 100%)}
  .pocket.is-flipped{transform:rotate(180deg)}
  .pocket__guide{position:absolute;border:1px solid rgba(154,214,234,.9)}
  .pocket--white .pocket__guide{left:32px;top:16px;width:392px;height:187px;border-top-left-radius:34px}
  .pocket--green .pocket__guide{left:40px;top:16px;width:380px;height:187px;border-top-right-radius:34px}

  .brand-lockup{position:absolute;left:176px;top:84px;display:flex;align-items:center;gap:8px}
  .brand-lockup__dot{width:38px;height:38px;border-radius:50%;border:3px solid var(--navy);background:#fff}
  .brand-lockup__name{font-family:"Raleway",sans-serif;font-weight:700;font-size:12px;color:var(--navy);line-height:1.05;width:70px}
  .brand-name{position:absolute;left:0;right:26px;top:160px;text-align:right;font-family:"Raleway",sans-serif;
    font-weight:800;font-size:20px;color:var(--navy)}
  .brand-sub{position:absolute;right:62px;top:186px;font-size:8px;color:var(--ink)}
  .crop{position:absolute;left:0;top:0}

  .pocket-copy{position:absolute;left:62px;top:36px;width:322px}
  .pocket-copy__bold{font-size:6px;font-weight:700;line-height:1.4;color:#111}
  .pocket-copy__body{margin-top:8px;font-size:5.6px;line-height:1.4;color:#222}
  .pocket-copy__head{margin-top:10px;font-family:"Fira Sans",sans-serif;font-weight:500;font-size:14px;line-height:1.3;color:#111}

  .pocket--top-left{left:99px;top:630px}
  .pocket--top-right{left:562px;top:630px}
  .pocket--bottom-left{left:99px;top:914px}
  .pocket--bottom-right{left:562px;top:914px}
</style>
</head>
<body>

<svg class="folder-body" width="1114" height="640" viewBox="0 0 1114 640">
  <path d="M58,53 L1050,53 L1056,60 L1056,398 A17,17 0 0 0 1056,432 L1056,622 L1044,630 L70,630 L58,622 L58,432 A17,17 0 0 0 58,398 Z"
        fill="#ffffff" stroke="#e0393e" stroke-width="0.8"/>
</svg>
<div class="fold-line fold-line--spine"></div>
<div class="guide guide--left"></div>
<div class="guide guide--right"></div>

<!-- Inside left panel -->
<div class="photo photo--beach" role="img" aria-label="Photo of a multi-generation family in white clothes walking hand in hand along a sunny beach"></div>
<div class="ribbon ribbon--left" role="img" aria-label="Pink and blue cancer awareness ribbon"></div>
<div class="intro">
  <p><strong>Hereditary cancer screening</strong> provides vital information to help people with a strong personal or family history of cancer understand their own risk of developing the disease. With this information, they can take steps to Potentially Prevent Cancer, Delay the Onset of Cancer or Catch it at an Earlier stage when outcomes and survival rates are Better.</p>
  <p class="intro__call">Don't be Afraid of the Answer: Knowledge is Power and Power Eradicates Fear. When You are Fearless, You Will Make all the Right Choices!</p>
</div>

<!-- Inside right panel -->
<div class="title-band"><div class="title-band__text">HEREDITARY CANCER SCREENING</div></div>
<div class="lead">
  <p class="lead__head">Doctors are the Gatekeepers to Genetic Testing.</p>
  <p class="lead__body">We have an obligation to help patients understand genetic risk and how testing can guide heath care decisions.</p>
</div>
<div class="photo photo--dinner" role="img" aria-label="Photo of a family of three generations sharing a meal at an outdoor table"></div>
<div class="ribbon ribbon--right" role="img" aria-label="Pink and blue cancer awareness ribbon"></div>
<div class="tag-band">
  <span class="tag-band__dot"></span>
  <span class="tag-band__text">The test you order FOR your patients</span>
</div>

<!-- Pockets -->
<div class="pocket pocket--white pocket--top-left is-flipped">
  <div class="pocket__sheet"></div>
  <div class="pocket__guide"></div>
  <svg class="crop" width="456" height="217"><g stroke="#e0393e" stroke-width="0.8">
    <line x1="128" y1="96" x2="158" y2="66"/><line x1="128" y1="150" x2="158" y2="180"/>
    <line x1="330" y1="66" x2="360" y2="96"/><line x1="330" y1="180" x2="360" y2="150"/></g></svg>
  <div class="brand-lockup"><span class="brand-lockup__dot"></span><span class="brand-lockup__name">Celvara Health Group</span></div>
  <div class="brand-name">Celvara Health Group</div>
  <div class="brand-sub">a division of Meridian Clinical Sales LLC</div>
</div>

<div class="pocket pocket--green pocket--top-right is-flipped">
  <div class="pocket__sheet"></div>
  <div class="pocket__guide"></div>
  <div class="pocket-copy">
    <p class="pocket-copy__bold">Getting tested brings clear benefits, whatever the result may be. If a relative, however distant, has had cancer, you may carry an inherited change that raises your own risk and may pass to your children. Carriers of such changes can face cancer earlier than others, so early testing lets risk be managed well.</p>
    <p class="pocket-copy__body">Hereditary cancer screening gives people with a strong personal or family history a clear view of their own risk, so they can act early to prevent cancer, delay its onset or find it at a stage when outcomes are better.</p>
    <p class="pocket-copy__head">Identifying an inherited genetic mutation has the potential to prevent cancer and save lives.</p>
  </div>
</div>

<div class="fold-line fold-line--pocket"></div>

<div class="pocket pocket--green pocket--bottom-left">
  <div class="pocket__sheet"></div>
  <div class="pocket__guide"></div>
  <div class="pocket-copy">
    <p class="pocket-copy__bold">Getting tested brings clear benefits, whatever the result may be. If a relative, however distant, has had cancer, you may carry an inherited change that raises your own risk and may pass to your children. Carriers of such changes can face cancer earlier than others, so early testing lets risk be managed well.</p>
    <p class="pocket-copy__body">Hereditary cancer screening gives people with a strong personal or family history a clear view of their own risk, so they can act early to prevent cancer, delay its onset or find it at a stage when outcomes are better.</p>
    <p class="pocket-copy__head">Identifying an inherited genetic mutation has the potential to prevent cancer and save lives.</p>
  </div>
</div>

<div class="pocket pocket--white pocket--bottom-right">
  <div class="pocket__sheet"></div>
  <div class="pocket__guide"></div>
  <svg class="crop" width="456" height="217"><g stroke="#e0393e" stroke-width="0.8">
    <line x1="128" y1="96" x2="158" y2="66"/><line x1="128" y1="150" x2="158" y2="180"/>
    <line x1="330" y1="66" x2="360" y2="96"/><line x1="330" y1="180" x2="360" y2="150"/></g></svg>
  <div class="brand-lockup"><span class="brand-lockup__dot"></span><span class="brand-lockup__name">Celvara Health Group</span></div>
  <div class="brand-name">Celvara Health Group</div>
  <div class="brand-sub">a division of Meridian Clinical Sales LLC</div>
</div>

</body>
</html>
```